Red Mesa Greenworks Summit needs a marketing flyer

We need a full page graphic for our upcoming Forum that can also be converted into a website "header" for social media, etc.: "Red Mesa Greenworks Summit - Shaping Change Across the Made Landscape"

INTRODUCTION:
During the first week of August 2022, Q-VarDT is presenting the Red Mesa Greenworks Summit - Shaping Change Across the Made Landscape.

One of the most exciting aspects of this conference will be the bringing together of multiple organizations including for-profits and nonprofits, K-12’s and higher education, cities and counties and other governmental agencies, as well as architects, engineers, and contractors to collaboratively present and discuss issues and ideas related to sustainability, with a Texas focus.

This event will be a catalyst for public and private project owners to holistically gather information and momentum as we bring the resources and vision needed to achieve the goal of zero carbon emissions from the built environment by 2040, and address water, green space and the natural environment, transportation, equity, and funding, among other topics.

```html
<!DOCTYPE html>
<html lang="en">
<head>
<meta charset="utf-8">
<title>Red Mesa Greenworks Summit – Flyer</title>
<link href="https://fonts.googleapis.com/css2?family=Anton&family=Montserrat:ital,wght@0,400;0,600;0,700;0,800;1,500&display=swap" rel="stylesheet">
<style>
  :root{
    --navy:#1c3c8c;
    --blue:#2452b0;
    --green:#7bb83a;
    --green-dark:#5d9a25;
    --ink:#26313f;
    --grey-box:#eef1f4;
    --stage:#1e1e1e;
    --white:#ffffff;
  }
  *{box-sizing:border-box;margin:0;padding:0}
  html,body{width:669px;height:1200px;overflow:hidden;background:var(--stage)}
  body{font-family:"Montserrat",Arial,sans-serif;color:var(--ink)}
  .flyer{position:absolute;left:24px;top:199px;width:620px;height:802px;background:var(--white);overflow:hidden}
  .brand{position:absolute;left:30px;top:30px;display:flex;align-items:center;gap:10px}
  .brand-mark{width:30px;height:30px;background:var(--navy)}
  .brand-name{font-weight:800;font-size:26px;color:var(--navy);letter-spacing:.5px}
  .hero-photo{position:absolute;left:340px;top:-60px}
  .title{position:absolute;left:30px;top:150px;font-family:"Anton",Impact,sans-serif;font-size:46px;line-height:1.05;color:var(--navy);text-transform:uppercase}
  .tagline{position:absolute;left:30px;top:310px;width:300px;font-size:15px;font-weight:600;line-height:1.3;color:var(--ink)}
  .presenting{position:absolute;left:0;top:360px;width:470px;height:72px;background:var(--green);padding:12px 20px 0 30px}
  .presenting-lead{font-family:"Anton",Impact,sans-serif;font-size:20px;color:var(--white);text-transform:uppercase;letter-spacing:.3px}
  .presenting-sub{font-size:10px;font-weight:700;color:var(--navy);text-transform:uppercase;margin-top:4px;line-height:1.25}
  .date-badge{position:absolute;left:478px;top:338px;width:112px;height:104px;background:var(--navy);color:var(--white);text-align:center;padding-top:20px;border-bottom:6px solid var(--green)}
  .date-small{font-size:10px;font-weight:600;text-transform:uppercase;line-height:1.3}
  .date-big{font-family:"Anton",Impact,sans-serif;font-size:22px;margin-top:6px}
  .intro{position:absolute;left:30px;top:458px;width:260px;font-size:9.5px;line-height:1.4;color:var(--blue);font-weight:600}
  .audience{position:absolute;left:30px;top:508px;width:240px;list-style:none}
  .audience li{display:flex;gap:6px;align-items:flex-start;font-size:9.5px;line-height:1.3;margin-bottom:6px}
  .audience svg{flex:none;margin-top:1px}
  .summary{position:absolute;left:318px;top:458px;width:272px;background:var(--grey-box);padding:14px 16px;font-size:10px;line-height:1.5;color:var(--ink);border-left:4px solid var(--green)}
  .venue{position:absolute;left:470px;top:640px;width:120px;font-size:9.5px;line-height:1.4;text-align:right;color:var(--ink)}
  .venue strong{color:var(--navy)}
  .contacts{position:absolute;left:30px;top:700px;display:flex;flex-direction:column;gap:6px}
  .phone{display:flex;align-items:center;gap:8px;background:var(--green);color:var(--white);font-size:11px;font-weight:700;padding:5px 12px 5px 8px;border-radius:14px;width:150px}
  .worker-photo{position:absolute;left:292px;top:632px;width:160px;height:140px;background:linear-gradient(180deg,#cfd8de 0%,#e8d34a 45%,#8a9aa8 100%)}
  .footer{position:absolute;left:0;bottom:0;width:620px;height:30px;background:var(--green)}
  .footer-web{position:absolute;right:0;top:0;height:30px;width:300px;background:var(--navy);color:var(--white);font-size:11px;font-weight:600;display:flex;align-items:center;justify-content:center}
</style>
</head>
<body>
<main class="flyer">
  <div class="brand">
    <span class="brand-mark"></span>
    <span class="brand-name">Q-VarDT</span>
  </div>

  <svg class="hero-photo" width="320" height="320" viewBox="0 0 320 320" role="img" aria-label="City skyline at sunset seen through office windows with silhouetted business people">
    <defs>
      <linearGradient id="skyline" x1="0" y1="0" x2="0" y2="1">
        <stop offset="0" stop-color="#9fb7cf"/>
        <stop offset=".55" stop-color="#e9c59a"/>
        <stop offset="1" stop-color="#4f6275"/>
      </linearGradient>
    </defs>
    <circle cx="180" cy="170" r="150" fill="none" stroke="var(--green)" stroke-width="10"/>
    <path d="M40 230 A150 150 0 0 0 300 260" fill="none" stroke="var(--navy)" stroke-width="10"/>
    <circle cx="180" cy="170" r="138" fill="url(#skyline)"/>
  </svg>

  <h1 class="title">Red Mesa<br>Greenworks<br>Summit</h1>
  <p class="tagline">Shaping Change Across the<br>Made Landscape</p>

  <section class="presenting">
    <p class="presenting-lead">Q-VarDT is presenting the Red Mesa</p>
    <p class="presenting-sub">Greenworks Summit – Shaping Change Across<br>the Made Landscape</p>
  </section>

  <div class="date-badge">
    <p class="date-small">During the<br>first week of</p>
    <p class="date-big">AUGUST 2022</p>
  </div>

  <p class="intro">One of the most exciting aspects of this conference will be the bringing together of multiple organizations including:</p>

  <ul class="audience">
    <li><svg width="10" height="10" viewBox="0 0 10 10"><path d="M1 5l3 3 5-7" fill="none" stroke="var(--green)" stroke-width="2"/></svg>For-profits and nonprofits</li>
    <li><svg width="10" height="10" viewBox="0 0 10 10"><path d="M1 5l3 3 5-7" fill="none" stroke="var(--green)" stroke-width="2"/></svg>K-12’s and higher education</li>
    <li><svg width="10" height="10" viewBox="0 0 10 10"><path d="M1 5l3 3 5-7" fill="none" stroke="var(--green)" stroke-width="2"/></svg>Cities and counties and other governmental agencies</li>
    <li><svg width="10" height="10" viewBox="0 0 10 10"><path d="M1 5l3 3 5-7" fill="none" stroke="var(--green)" stroke-width="2"/></svg>As well as architects</li>
    <li><svg width="10" height="10" viewBox="0 0 10 10"><path d="M1 5l3 3 5-7" fill="none" stroke="var(--green)" stroke-width="2"/></svg>Engineers</li>
    <li><svg width="10" height="10" viewBox="0 0 10 10"><path d="M1 5l3 3 5-7" fill="none" stroke="var(--green)" stroke-width="2"/></svg>Contractors to collaboratively present and discuss issues and ideas related to sustainability</li>
    <li><svg width="10" height="10" viewBox="0 0 10 10"><path d="M1 5l3 3 5-7" fill="none" stroke="var(--green)" stroke-width="2"/></svg>With a Texas focus</li>
  </ul>

  <p class="summary">This event will be a catalyst for public and private project owners to holistically gather information and momentum as we bring the resources and vision needed to achieve the goal of zero carbon emissions from the built environment by 2040, and address water, green space and the natural environment, transportation, equity, and funding, among other topics.</p>

  <p class="venue"><strong>Q-VarDT</strong><br>418 Cedar Loop<br>Alvarado, TX 76009</p>

  <div class="contacts">
    <span class="phone"><svg width="12" height="12" viewBox="0 0 24 24"><path d="M6.6 10.8a15 15 0 006.6 6.6l2.2-2.2a1 1 0 011-.25 11.4 11.4 0 003.6.6 1 1 0 011 1V20a1 1 0 01-1 1A17 17 0 013 4a1 1 0 011-1h3.5a1 1 0 011 1c0 1.25.2 2.45.6 3.6a1 1 0 01-.25 1z" fill="var(--white)"/></svg>(555) 014-2281</span>
    <span class="phone"><svg width="12" height="12" viewBox="0 0 24 24"><path d="M6.6 10.8a15 15 0 006.6 6.6l2.2-2.2a1 1 0 011-.25 11.4 11.4 0 003.6.6 1 1 0 011 1V20a1 1 0 01-1 1A17 17 0 013 4a1 1 0 011-1h3.5a1 1 0 011 1c0 1.25.2 2.45.6 3.6a1 1 0 01-.25 1z" fill="var(--white)"/></svg>(555) 014-7736</span>
  </div>

  <div class="worker-photo" role="img" aria-label="Construction engineer in hard hat and high-visibility vest"></div>

  <footer class="footer">
    <div class="footer-web">www.qvardt-summit.org</div>
  </footer>
</main>
</body>
</html>
```